Presentation Folder, for Cancer Awareness, VERY COLORFULL AND MODERN

This will be a standard size folder that will hold standard 8 1/2 x 11 papers with a business card slot on the flap, this is a very easy project with very little text and the design for the back page is already done so all you really have to do is make a very nice colorful front cover, you will see my attachments are labeled and I gave you alot of instructions, this should be a very fast easy project
Updates

Reason: there has not been enough quality designs, sorry

Target Market(s)

Our Target Market is Dr's that Deal with Cancer patients

Industry/Entity Type

Healthcare

Font styles to use
Serif

Colors

Designer to choose colors to be used in the design.

Requirements
Must have
• Project must be tasteful and look professional with the ribbons as the main focal point in the center of folder the folder should be a nice gray color to accent the color of the ribbons , the back page needs no design it is the" Sorvane Test" in the attachments I sent
Nice to have
• I would like the ribbons displayed in a row, I included a logo sample layout
• a picture on the front of the folder under the words Hereditary Cancer Screening - Then under that put the words - The Power of Knowledge - then add the picture I labeled Great Picture in the attachments

```html
<!DOCTYPE html>
<html lang="en">
<head>
<meta charset="utf-8">
<title>Hereditary Cancer Screening Folder</title>
<link rel="stylesheet" href="https://fonts.googleapis.com/css2?family=Arimo:wght@400;700&family=Montserrat:wght@400;500;600&family=Roboto+Condensed:wght@400;700&display=swap">
<style>
  :root{
    --backdrop:#ececec;
    --paper:#ffffff;
    --brand-red:#e8322f;
    --ink:#111111;
    --muted:#7a7a7a;
    --header-gray:#5b5c5e;
    --row-alt:#e7e7e7;
    --lynch:#f6c340;
    --peutz:#a9c23c;
    --lifraumeni:#3ea24f;
    --cowden:#1c9cd8;
    --gastric:#5f605f;
  }
  *{box-sizing:border-box;margin:0;padding:0}
  html,body{width:1200px;height:1000px;overflow:hidden}
  body{background:var(--backdrop);position:relative;font-family:"Arimo",Arial,sans-serif}
  .panel{position:absolute;top:160px;width:500px;height:668px;background:var(--paper);box-shadow:0 2px 10px rgba(0,0,0,.12)}
  .front-cover{left:60px}
  .back-page{left:640px}

  .brand{display:flex;flex-direction:column;align-items:center;gap:10px}
  .brand-dot{width:38px;height:38px;border-radius:50%;background:var(--brand-red)}
  .brand-name{font-family:"Montserrat",sans-serif;font-weight:400;color:var(--brand-red);letter-spacing:5px;font-size:19px}
  .front-cover .brand{position:absolute;top:60px;left:0;right:0}

  .cover-title{position:absolute;top:250px;left:0;right:0;text-align:center;font-family:"Arimo",sans-serif;font-weight:700;font-size:27px;color:var(--ink);letter-spacing:-.3px}
  .ribbon-art{position:absolute;top:335px;left:30px;width:440px;height:250px;border-radius:6px;
    background:linear-gradient(90deg,#f4e34a,#bdbdbd,#ee90ac,#62c6c8,#a8d8e0,#9b4fd6,#3a3fc6,#7a3f12);
    opacity:.85}
  .ribbon-art::after{content:"";position:absolute;left:0;right:0;bottom:0;height:50%;border-radius:0 0 6px 6px;
    background:linear-gradient(90deg,#f48c8c,#78b52a,#2166b8,#eeeeee,#1b1b1b,#8fd2f2,#8f99e6)}
  .tagline{position:absolute;top:620px;left:0;right:0;text-align:center;font-family:"Montserrat",sans-serif;font-size:19px;letter-spacing:4.5px;color:var(--brand-red)}

  .menu-title{position:absolute;top:26px;left:0;right:0;text-align:center;font-family:"Montserrat",sans-serif;font-weight:500;font-size:29px;color:var(--brand-red);line-height:1}
  .menu-title sup{font-size:11px;vertical-align:super}
  .menu-sub{position:absolute;top:60px;left:0;right:0;text-align:center;font-family:"Montserrat",sans-serif;font-size:12px;letter-spacing:1px;color:var(--muted)}
  .gene-table{position:absolute;top:84px;left:42px;width:416px;border-collapse:collapse;font-family:"Roboto Condensed",sans-serif;font-size:8px;line-height:11.2px;box-shadow:1px 1px 3px rgba(0,0,0,.25)}
  .gene-table td,.gene-table th{padding:0 6px;height:11.2px;text-align:left;white-space:nowrap}
  .gene-table td:first-child{width:100px;color:var(--brand-red);font-weight:700}
  .gene-table td:last-child{color:#333}
  .gene-table tbody tr:nth-child(even){background:var(--row-alt)}
  .col-gene{background:var(--brand-red);color:#fff;font-weight:700}
  .col-organ{background:var(--header-gray);color:#fff;font-weight:700}
  .syndrome th{color:#fff;font-weight:700}
  .syndrome.lynch th{background:var(--lynch)}
  .syndrome.peutz th{background:var(--peutz)}
  .syndrome.lifraumeni th{background:var(--lifraumeni)}
  .syndrome.cowden th{background:var(--cowden)}
  .syndrome.gastric th{background:var(--gastric)}
  .back-footer{position:absolute;top:592px;left:0;right:0;display:flex;justify-content:center;align-items:center;gap:12px}
  .back-footer .brand-dot{width:30px;height:30px}
  .back-footer .brand-name{font-size:16px;letter-spacing:4px}
  .contact-line{font-family:"Arimo",sans-serif;font-size:5.5px;color:#555;line-height:8px;margin-top:2px}
</style>
</head>
<body>
  <section class="panel front-cover">
    <div class="brand"><span class="brand-dot"></span><span class="brand-name">CORVITA LABS</span></div>
    <h1 class="cover-title">Hereditary Cancer Screening</h1>
    <div class="ribbon-art" role="img" aria-label="Two rows of colourful cancer awareness ribbons"></div>
    <p class="tagline">THE POWER OF KNOWLEDGE</p>
  </section>

  <section class="panel back-page">
    <h2 class="menu-title">SORVANE<sup>™</sup> Test Menu</h2>
    <p class="menu-sub">CLIA# 22D4817305 | CORVITALABS.COM</p>
    <table class="gene-table">
      <thead><tr><th class="col-gene">GENE</th><th class="col-organ">CANCER-ASSOCIATED ORGAN/SYSTEMS</th></tr></thead>
      <tbody>
        <tr><td>APC</td><td>Colon</td></tr>
        <tr><td>ATM</td><td>Breast/Pancreatic/Brain</td></tr>
        <tr><td>BARD1</td><td>Breast/Ovarian</td></tr>
        <tr><td>BMPR1A</td><td>Colon</td></tr>
        <tr><td>BRCA1</td><td>Breast/Ovarian/Prostate</td></tr>
        <tr><td>BRCA2</td><td>Breast/Ovarian/Prostate</td></tr>
        <tr><td>BRIP1</td><td>Breast/Ovarian</td></tr>
        <tr><td>CDK4</td><td>Melanoma</td></tr>
        <tr><td>P16 (CDKN2A)</td><td>Melanoma/Breast/Pancreatic/Squamous</td></tr>
        <tr><td>FANCC</td><td>Blood</td></tr>
        <tr><td>MEN1</td><td>Thyroid/Parathyroid</td></tr>
        <tr><td>MET</td><td>Renal/Hepatic</td></tr>
        <tr><td>MRE11A</td><td>Ovarian/Breast</td></tr>
        <tr><td>NBN</td><td>Breast/Ovarian/Prostate/Melanoma</td></tr>
        <tr><td>NF1</td><td>Blood</td></tr>
        <tr><td>NTRK1</td><td>Thyroid/Parathyroid</td></tr>
        <tr><td>PALB2</td><td>Breast/Ovarian/Pancreatic</td></tr>
        <tr><td>PTCH1</td><td>Melanoma/Brain/Breast/Colon</td></tr>
        <tr><td>RAD50</td><td>Breast/Ovarian</td></tr>
        <tr><td>RAD51C</td><td>Ovarian/Breast</td></tr>
        <tr><td>RAD51D</td><td>Ovarian/Breast</td></tr>
        <tr><td>RET</td><td>Lung/Thyroid/Parathyroid</td></tr>
        <tr><td>SMAD4</td><td>Colon/Pancreas</td></tr>
      </tbody>
      <tbody>
        <tr class="syndrome lynch"><th colspan="2">LYNCH SYNDROME GENES</th></tr>
        <tr><td>MLH1</td><td>Colorectal/Ovarian</td></tr>
        <tr><td>MSH2</td><td>Colorectal/Ovarian</td></tr>
        <tr><td>MSH6</td><td>Colorectal/Ovarian</td></tr>
        <tr><td>PMS2</td><td>Colorectal/Ovarian</td></tr>
        <tr><td>EPCAM</td><td>Colorectal</td></tr>
      </tbody>
      <tbody>
        <tr class="syndrome peutz"><th colspan="2">PEUTZ-JEGHERS SYNDROME GENE</th></tr>
        <tr><td>STK11</td><td>Breast/Ovarian/Melanoma/Colorectal/Lung</td></tr>
      </tbody>
      <tbody>
        <tr class="syndrome lifraumeni"><th colspan="2">LI-FRAUMENI SYNDROME GENE</th></tr>
        <tr><td>CHEK2</td><td>Breast/Ovarian/Prostate</td></tr>
        <tr><td>PT53</td><td>Breast/Bladder/Ovarian/Squamous</td></tr>
      </tbody>
      <tbody>
        <tr class="syndrome cowden"><th colspan="2">COWDEN SYNDROME GENE</th></tr>
        <tr><td>PTEN</td><td>Endometrium/Breast/Prostate/Lung</td></tr>
      </tbody>
      <tbody>
        <tr class="syndrome gastric"><th colspan="2">HEREDITARY DIFFUSE GASTRIC CANCER SYNDROME GENE</th></tr>
        <tr><td>CDH1</td><td>Breast/Gastric/Ovarian/Prostate</td></tr>
        <tr><td>VHL</td><td>Renal</td></tr>
      </tbody>
    </table>
    <footer class="back-footer">
      <span class="brand-dot"></span>
      <div>
        <span class="brand-name">CORVITA LABS</span>
        <p class="contact-line">220 MERIDIAN WAY | SUITE B | HALDEN, GA 30000<br>tel 404.555.0142 | fax 404.555.0198 | info@corvitalabs.com</p>
      </div>
    </footer>
  </section>
</body>
</html>
```